Business Card Design

Attached is my current Business card I do not like it but I must save the logo portion of it. Don't like the color or the lettering am looking for more architectural look in grays or taupe with the green more of a charturese color and the blue a charcoal color on a textured paper that looks more like something high-end that would appeal to an architect or a designer. We make concrete decorative items such as concrete fireplaces, sinks, tops and more.

Target Market(s)

Architects designers of Commercial and Residential - artistic features

Industry/Entity Type

Architect

Contact Information for Business Card

Marisol T. Quenby President and Marketing Director
602-418-5093
email marisol@vantorelstone.example
Showroom "Quillmont Design Center" 4183 W Palomar Scottsdale AZ
Fax: 602-731-6624

Font styles to use
Sans Serif

Requirements
Must have
• Architectural
Natural and earthy colors with a touch of color in the existing attached

```html
<!DOCTYPE html>
<html lang="en">
<head>
<meta charset="utf-8">
<title>Vantorel Stone — Business Card</title>
<link rel="stylesheet" href="https://fonts.googleapis.com/css2?family=Titillium+Web:wght@300;400&display=swap">
<style>
  :root {
    --backdrop: #d9d6d1;
    --charcoal: #1f2835;
    --charcoal-soft: #263140;
    --chartreuse: #93b52c;
    --paper: #ecebe8;
    --ink-light: #f1f2f2;
    --ink-muted: #c9ced4;
    --ink-gray: #4c5560;
  }
  * { margin: 0; padding: 0; box-sizing: border-box; }
  html, body {
    width: 1200px; height: 1000px; overflow: hidden;
    background: var(--backdrop);
    font-family: "Titillium Web", sans-serif;
  }
  .card {
    position: absolute; left: 250px;
    width: 700px; height: 400px;
    overflow: hidden;
    box-shadow: 0 10px 28px rgba(0,0,0,.22);
  }
  .card--back { top: 60px; background: var(--charcoal); }
  .card--front { top: 540px; background: var(--charcoal); }
  .card svg.bands { position: absolute; inset: 0; }

  .wordmark {
    position: absolute; text-align: left;
    text-transform: uppercase; font-weight: 300; letter-spacing: 1px;
    white-space: nowrap;
  }
  .wordmark__name { display: flex; align-items: center; gap: 10px; }
  .wordmark__square { width: 14px; height: 14px; background: var(--chartreuse); }
  .wordmark__sub { text-transform: none; font-size: 16px; padding-left: 24px; }

  .card--back .wordmark { left: 215px; top: 150px; color: var(--ink-light); font-size: 32px; }
  .card--back .wordmark__sub { font-size: 18px; }
  .card--front .wordmark { left: 30px; top: 170px; color: var(--ink-gray); font-size: 22px; }

  .holder {
    position: absolute; left: 322px; top: 164px;
    color: var(--ink-light); white-space: nowrap;
  }
  .holder__name { font-size: 24px; font-weight: 300; line-height: 1.15; }
  .holder__title { font-size: 12px; color: var(--ink-muted); font-weight: 300; }

  .contact {
    position: absolute; left: 522px; top: 158px;
    border-left: 2px solid var(--chartreuse);
    padding-left: 10px;
    list-style: none; color: var(--ink-muted);
    font-size: 10px; font-weight: 300; line-height: 20px;
  }
  .contact li { display: flex; align-items: center; gap: 5px; white-space: nowrap; }
  .contact svg { width: 9px; height: 9px; fill: var(--chartreuse); flex: none; }
</style>
</head>
<body>

<section class="card card--back" aria-label="Card back">
  <svg class="bands" width="700" height="400" viewBox="0 0 700 400">
    <polygon points="0,0 700,0 700,250 0,330" fill="var(--charcoal-soft)" opacity=".5"/>
    <polygon points="0,355 700,265 700,300 0,400" fill="var(--chartreuse)"/>
  </svg>
  <div class="wordmark">
    <div class="wordmark__name"><span class="wordmark__square"></span>Vantorel Stone</div>
    <div class="wordmark__sub">Design Studio</div>
  </div>
</section>

<section class="card card--front" aria-label="Card front">
  <svg class="bands" width="700" height="400" viewBox="0 0 700 400">
    <polygon points="0,0 240,0 320,400 0,400" fill="var(--paper)"/>
    <polygon points="240,0 268,0 348,400 320,400" fill="var(--chartreuse)"/>
  </svg>
  <div class="wordmark">
    <div class="wordmark__name"><span class="wordmark__square"></span>Vantorel Stone</div>
    <div class="wordmark__sub">Design Studio</div>
  </div>
  <div class="holder">
    <div class="holder__name">Marisol T. Quenby</div>
    <div class="holder__title">President &amp; Marketing Director</div>
  </div>
  <ul class="contact">
    <li><svg viewBox="0 0 10 10"><path d="M2 0h2l1 3-1.5 1a6 6 0 0 0 2.5 2.5L7 5l3 1v2c0 1-1 2-2 2A8 8 0 0 1 0 2c0-1 1-2 2-2z"/></svg>602-418-5093</li>
    <li><svg viewBox="0 0 10 10"><path d="M2 0h5v3H2zM0 4h10v5H0zM3 6h4v3H3z"/></svg>602-731-6624</li>
    <li><svg viewBox="0 0 10 10"><path d="M0 2h10v6H0zM0 2l5 3.5L10 2" stroke="var(--charcoal)" stroke-width=".8"/></svg>marisol@vantorelstone.example</li>
  </ul>
</section>

</body>
</html>
```